Yoga Workshop - Yoga Practice information flyer

I am a yoga teacher who will be presenting a workshop on yoga for sleep and need a brochure for my clients which outlines a practice that I give them so they can do the practice at home. Ideally I would like a brochure that is a single A3 size of paper in size that folds in half to an A4 booklet with the entire practice on the centre section to make it easy for people to do the practice at home with just one open page in front of them:
* Front page detailing "Yoga for Sleep Workshop" and "Restorative Yoga Practice"
* Centre contains the information on the practice contained in the attached word document. The practice consists of 5 postures, so there needs to be five separate sections which have the pictures of the postures (attached in uploaded files) and the wording contained in the attached word document. All pictures uploaded need to be included in the flyer as each posture has different pictures demonstrating the posture using yoga props or using things people have at home
* Back page containing a picture of myself (picture uploaded in files) with some information about me (contained in the attached word document) and my website www.calmdrift.com.au

I also need this flyer to be able to printed on 2 double sided A4 sheets of paper so will require 2 x pdf file versions. Importantly, for the centre section of the flyer, the design needs to ensure if it is printed on A4 paper, the wording and pictures for each of the postures are not separated over two pages

Target Market(s)

Existing clients

Requirements
Must have
• Detailed in project description
Nice to have
• The word document also contains some quotes. These do not need to be included in the flyer. If there is room and there is room for one or two of those please include where it would look good
Should not have
• Stock pictures of people in yoga postures which a normal everyday person could not get into

```html
<!DOCTYPE html>
<html lang="en">
<head>
<meta charset="utf-8">
<title>Restorative Yoga Practice – Postures 1 and 2</title>
<link rel="stylesheet" href="https://fonts.googleapis.com/css2?family=Josefin+Sans:ital,wght@0,400;0,700;1,400&display=swap">
<style>
  :root {
    --navy: #34485f;
    --terracotta: #c98764;
    --gold: #f6c93f;
    --white: #ffffff;
    --photo-tone-a: #8a5535;
    --photo-tone-b: #6f4a3d;
  }
  * { margin: 0; padding: 0; box-sizing: border-box; }
  html, body { width: 848px; height: 1200px; overflow: hidden; }
  body { background: var(--navy); font-family: "Josefin Sans", sans-serif; color: var(--white); }
  .page { position: relative; width: 848px; height: 1200px; overflow: hidden; background: var(--navy); }
  .lower-band { position: absolute; left: 0; top: 0; width: 848px; height: 1200px; }
  .photo-frame {
    position: absolute; width: 231px; height: 357px;
    background: var(--white); padding: 5px;
  }
  .photo {
    width: 100%; height: 100%;
    background: linear-gradient(170deg, var(--photo-tone-a) 0%, var(--photo-tone-b) 100%);
  }
  .posture { position: absolute; left: 35px; width: 770px; }
  .posture-title {
    font-weight: 700; color: var(--gold); font-size: 19.3px;
    letter-spacing: .4px; line-height: 1; margin-bottom: 16px;
  }
  .posture p {
    font-size: 14.2px; line-height: 15.7px; letter-spacing: .6px;
    margin-bottom: 15.5px;
  }
  .label { font-style: italic; color: var(--gold); }
</style>
</head>
<body>
<main class="page">
  <svg class="lower-band" viewBox="0 0 848 1200" aria-hidden="true">
    <path d="M0 672 Q424 575 848 672 L848 1200 L0 1200 Z" fill="var(--terracotta)"/>
  </svg>

  <div class="photo-frame" style="left:35px; top:29px;"><div class="photo" role="img" aria-label="Woman lying on a yoga mat with a bolster under her knees and a cushion under her head"></div></div>
  <div class="photo-frame" style="left:302px; top:29px;"><div class="photo" role="img" aria-label="Woman lying on a yoga mat with a rolled towel under her knees"></div></div>
  <div class="photo-frame" style="left:570px; top:29px;"><div class="photo" role="img" aria-label="Woman sitting on the mat in front of a lengthways rolled towel, ready to lie back"></div></div>

  <section class="posture" style="top:411px;">
    <h2 class="posture-title">Posture 1 - Supported Chest Opening with Knee Support</h2>
    <p><span class="label">Props</span> - 2 x bolsters (or towels rolled up lengthways), 1 x cushion for head support (optional)</p>
    <p><span class="label">Set up notes</span> - Position the props in a T-position with one bolster/towel running parallel to the yoga mat and one bolster towel running horizontal to the mat underneath the knees.&nbsp; Position yourself so your buttocks is on the floor and the parallel bolster runs from the lower back up to behind the head.</p>
    <p><span class="label">Caution</span> - If any lower back pain is experience adjust the parallel bolster height by using a towel.&nbsp; If using a towel, the height of the parallel support prop can be adjusted by either using a thinner towel or loosely rolling the towel.&nbsp; Do not us any parallel support prop if pain continues.</p>
  </section>

  <div class="photo-frame" style="left:171px; top:613px;"><div class="photo" role="img" aria-label="Woman in supported bound-angle pose with yoga blocks under her knees"></div></div>
  <div class="photo-frame" style="left:439px; top:613px;"><div class="photo" role="img" aria-label="Woman in supported bound-angle pose with pillows under her knees"></div></div>

  <section class="posture" style="top:995px;">
    <h2 class="posture-title">Posture 2 - Supported Bound-Angle Pose</h2>
    <p><span class="label">Props</span> - 1 x bolsters (or towel rolled up lengthways), 2 x yoga blocks/bolsters (or pillows), 1 x cushion for head support (optional)</p>
    <p><span class="label">Set up notes</span> - Similar to Posture 1 without the bolster behind the knees.&nbsp; Instead, the soles of the feet are together with knees wide being supported by either blocks, bolsters or pillows.</p>
    <p><span class="label">Caution</span> - If any lower back pain is experience adjust the parallel bolster height by using a towel.&nbsp; If using a towel, the height of the parallel support prop can be adjusted by either using a thinner towel or loosely rolling the towel.&nbsp; Do not us any parallel support prop if pain continues.</p>
  </section>
</main>
</body>
</html>
```